Business Card for Vorla Parts Wholesale supplier

Hi There! I need a new business card for our company. We are specialized in selling Vorla parts, mostly we sell new LCD screens for Zelnar and Drelks. I would like to see that back in the design.

You can find the colors and logo's on our website: www.hartuvo.nl

Industry/Entity Type

Business

Contact Information for Business Card

My Details:
Tobias Lindqvist

Phone: 0031687203316
E-mail: Tobias@hartuvo.nl

Slogan: "Because Quality Matters"

Font styles to use
Sans Serif

Colors

Designer to choose colors to be used in the design.

Requirements
Must have
• A Black backside with the Hartuvo logo on it. The front side should be clean with only my contact details.
• But I'm also open for something really different or awesome!
Nice to have
• Remember that we are in the parts & repairing industry, So i'll be handing those business cards mainly to repair companies. Maybe you can do something with that thought :)

```html
<!DOCTYPE html>
<html lang="en">
<head>
<meta charset="utf-8">
<title>Hartuvo Business Card</title>
<link rel="stylesheet" href="https://fonts.googleapis.com/css2?family=Saira:wght@400;500;600&display=swap">
<style>
  :root {
    --backdrop: #b3b3b3;
    --card-white: #ffffff;
    --card-dark: #282828;
    --brand-orange: #f36f21;
    --ink: #111111;
    --mark-grey: #9a9a9a;
    --shadow: rgba(0, 0, 0, 0.35);
  }
  * { margin: 0; padding: 0; box-sizing: border-box; }
  html, body {
    width: 1200px;
    height: 900px;
    overflow: hidden;
    background: var(--backdrop);
    font-family: "Saira", sans-serif;
  }
  .stage { position: relative; width: 1200px; height: 900px; }
  .card {
    position: absolute;
    top: 271px;
    width: 459px;
    height: 281px;
    border-radius: 14px;
    overflow: hidden;
    box-shadow: 2px 3px 5px var(--shadow);
  }
  .card--front { left: 137px; background: var(--card-white); }
  .card--back { left: 626px; background: var(--card-dark); }

  .front__panel {
    position: absolute;
    top: 0; right: 0;
    width: 95px; height: 100%;
    background: var(--card-dark);
  }
  .front__accent {
    position: absolute;
    left: 280px; top: 88px;
    width: 104px; height: 104px;
    border-radius: 50%;
    background: var(--brand-orange);
    border: 6px solid var(--card-white);
  }
  .brand {
    position: absolute;
    display: flex;
    align-items: center;
  }
  .brand__dot { flex: none; }
  .brand__name { font-weight: 500; line-height: 1; letter-spacing: 0.5px; }

  .front__brand { left: 28px; top: 27px; gap: 12px; }
  .front__brand .brand__dot {
    width: 40px; height: 40px; border-radius: 50%;
    background: var(--brand-orange);
  }
  .front__brand .brand__name { font-size: 44px; color: var(--ink); }

  .tagline {
    position: absolute;
    left: 27px; top: 95px;
    font-size: 15px;
    color: var(--brand-orange);
  }
  .contact-name {
    position: absolute;
    left: 27px; top: 161px;
    font-size: 21px;
    font-weight: 600;
    color: var(--brand-orange);
  }
  .contact-list {
    position: absolute;
    left: 28px; top: 199px;
    list-style: none;
  }
  .contact-list li {
    display: flex;
    align-items: center;
    gap: 7px;
    height: 21px;
    font-size: 13px;
    color: var(--ink);
  }
  .contact-list svg { width: 13px; height: 13px; flex: none; }

  .back__brand {
    left: 50%; top: 50%;
    transform: translate(-50%, -50%);
    gap: 12px;
  }
  .back__brand .brand__dot {
    width: 58px; height: 58px; border-radius: 8px;
    background: var(--mark-grey);
  }
  .back__brand .brand__name { font-size: 58px; color: var(--card-white); }
</style>
</head>
<body>
<main class="stage">
  <section class="card card--front" aria-label="Business card front">
    <div class="front__panel"></div>
    <div class="front__accent"></div>
    <div class="brand front__brand">
      <span class="brand__dot"></span>
      <span class="brand__name">hartuvo</span>
    </div>
    <p class="tagline">Because Quality Matters</p>
    <h1 class="contact-name">Tobias Lindqvist</h1>
    <ul class="contact-list">
      <li>
        <svg viewBox="0 0 14 14" aria-hidden="true"><circle cx="7" cy="7" r="7" fill="#f36f21"/><path d="M4 5.5h6v1.2H4zM5 6.7h4v2.8H5z" fill="#fff"/></svg>
        0031687203316
      </li>
      <li>
        <svg viewBox="0 0 14 14" aria-hidden="true"><circle cx="7" cy="7" r="7" fill="#f36f21"/><rect x="3.8" y="4.8" width="6.4" height="4.4" fill="#fff"/><path d="M3.8 4.8L7 7.3l3.2-2.5" fill="none" stroke="#f36f21" stroke-width="0.8"/></svg>
        Tobias@hartuvo.nl
      </li>
      <li>
        <svg viewBox="0 0 14 14" aria-hidden="true"><circle cx="7" cy="7" r="7" fill="#f36f21"/><circle cx="7" cy="7" r="3.2" fill="none" stroke="#fff" stroke-width="1"/><path d="M3.8 7h6.4M7 3.8v6.4" stroke="#fff" stroke-width="0.7"/></svg>
        www.hartuvo.nl
      </li>
    </ul>
  </section>

  <section class="card card--back" aria-label="Business card back">
    <div class="brand back__brand">
      <span class="brand__dot"></span>
      <span class="brand__name">hartuvo</span>
    </div>
  </section>
</main>
</body>
</html>
```